Winelabel for Italian Wine incl. box.

Front and back label for new Italian wine.
It´s a premium redwine,
Size of Labels: Front 100x115 | Back 60x85
For front label we can also use these sizes:
95X115 - 100x100 – 86x97 – 100x110
For back labels : 60X90 – 60X95 – 60X100
We can only use one type of foil finishing.
BRAND = CREDALI sul` Passo Vellino (in 2 lines)
2. titel = Vino della Serpola
Semi lines = Ancient vinification Traditions | Truscany
Style = elegant Italian coloured Harlequin,
Other colors using white/black/gold
Include a round "water-mark" with text : Selected for loyal winelowers
Back label will be short story + legal data + barcode.
Outer box of 6 bottles case design print on all 4 fronts.

```html
<!DOCTYPE html>
<html lang="it">
<head>
<meta charset="utf-8">
<title>Credali sul` Passo Vellino – Front Label</title>
<link href="https://fonts.googleapis.com/css2?family=Cormorant+Garamond:wght@400;500&family=Marcellus&display=swap" rel="stylesheet">
<style>
  :root {
    --backdrop: #14253a;
    --paper: #f7f7f5;
    --ink: #1d2024;
    --ink-soft: #4a4d52;
    --gold: #b8923f;
    --band: #2b2d31;
    --band-light: #5b5e63;
    --wash-dark: #3a3c40;
    --wash-light: #d9dadc;
  }
  * { margin: 0; padding: 0; box-sizing: border-box; }
  html, body {
    width: 1200px; height: 860px; overflow: hidden;
    background: var(--backdrop);
  }
  .stage {
    width: 1200px; height: 860px;
    display: flex; align-items: center; justify-content: center;
  }
  .front-label {
    position: relative;
    width: 600px; height: 690px;
    background: var(--paper);
    overflow: hidden;
  }
  .gold-rule-top {
    position: absolute; left: 0; right: 0; top: 22px;
    height: 2px; background: var(--gold);
  }
  .landscape-wash {
    position: absolute; left: 120px; top: 110px;
    width: 290px; height: 260px;
    border-radius: 46% 54% 40% 60% / 50% 44% 56% 50%;
    background: radial-gradient(ellipse at 40% 55%, var(--wash-dark) 0%, #7c7e82 45%, var(--wash-light) 75%, rgba(247,247,245,0) 100%);
  }
  .brand-name {
    position: absolute; left: 80px; top: 330px;
    font-family: "Cormorant Garamond", serif;
    font-weight: 500; font-size: 104px; letter-spacing: 2px;
    color: var(--ink); line-height: 1;
  }
  .brand-sub {
    position: absolute; left: 86px; top: 448px;
    font-family: "Marcellus", serif;
    font-size: 30px; letter-spacing: 9px;
    color: var(--ink); text-transform: uppercase;
  }
  .seal-text {
    position: absolute; left: 0; top: 470px; width: 600px; height: 120px;
  }
  .seal-text text {
    font-family: "Marcellus", serif; font-size: 15px; letter-spacing: 5px;
    fill: var(--ink-soft);
  }
  .bottom-band {
    position: absolute; left: 0; right: 0; bottom: 0; height: 92px;
    background: linear-gradient(180deg, var(--band-light) 0%, var(--band) 55%, #1a1b1e 100%);
    border-top: 2px solid var(--gold);
    display: flex; align-items: center; justify-content: center;
  }
  .wine-title {
    font-family: "Cormorant Garamond", serif;
    font-size: 30px; letter-spacing: 8px;
    color: #e8e8e6;
  }
</style>
</head>
<body>
  <main class="stage">
    <section class="front-label">
      <div class="gold-rule-top"></div>
      <div class="landscape-wash" role="img" aria-label="Monochrome watercolour of Tuscan hills with cypress trees"></div>
      <h1 class="brand-name">CREDALI</h1>
      <p class="brand-sub">sul` Passo Vellino</p>
      <svg class="seal-text" viewBox="0 0 600 120" aria-label="Selected for loyal winelowers">
        <defs>
          <path id="seal-arc" d="M60,40 Q300,120 540,40" fill="none"/>
        </defs>
        <text><textPath href="#seal-arc" startOffset="50%" text-anchor="middle">SELECTED FOR LOYAL WINELOWERS</textPath></text>
      </svg>
      <div class="bottom-band">
        <p class="wine-title">Vino della Serpola</p>
      </div>
    </section>
  </main>
</body>
</html>
```